Satchel & Sundial needs new business card design

I need a new business card design. I'm looking for out-of-the-box design which represents the freedom of being a location independent entrepreneur.
I offer coaching, retreats and trips.
I would like to see designs with and without the photo.
Colors I use are black (#000000), green (#25A796) and brown (#D7C38C)
Website satchelandsundial.example

Target Market(s)

location independent entrepreneurs, digital nomads, people looking to swap the 9 to 5 for a lifestyle business

Industry/Entity Type

Business

Contact Information for Business Card

Dorota Falkner
Your Lifestyle Business Coach, Retreat & Trip Leader
http://satchelandsundial.example
hello@satchelandsundial.example
Live a life you don't need a holiday from

Font styles to use
Serif
Sans Serif

Requirements
Must have
• One side should contain only the logo. I would also consider having the "Live a life you don't need a holiday from" on that side too (depending on how it looks)
• Please show both sides on the designs.

```html
<!DOCTYPE html>
<html lang="en">
<head>
<meta charset="utf-8">
<title>Satchel &amp; Sundial — Business Card</title>
<link rel="stylesheet" href="https://fonts.googleapis.com/css2?family=Source+Sans+3:wght@400;600;700&display=swap">
<style>
  :root {
    --teal: #25a796;
    --ink: #231f20;
    --white: #ffffff;
    --paper: #ececec;
    --stage: #f4f2ef;
  }
  html, body {
    margin: 0;
    padding: 0;
    width: 1200px;
    height: 900px;
    overflow: hidden;
    background: var(--stage);
    font-family: "Source Sans 3", Arial, sans-serif;
  }
  .canvas {
    position: relative;
    width: 1200px;
    height: 900px;
  }
  .card {
    position: absolute;
    width: 556px;
    height: 343px;
    overflow: hidden;
    box-shadow: 0 6px 18px rgba(0,0,0,0.12);
  }
  /* Front side */
  .card-front {
    left: 237px;
    top: 62px;
    background: var(--teal);
    border-radius: 0 52px 0 42px;
  }
  .front-band {
    position: absolute;
    left: 0;
    top: 146px;
    width: 100%;
    height: 197px;
    background: var(--ink);
  }
  .front-diagonal {
    position: absolute;
    left: 0;
    top: 0;
  }
  .brand-name {
    margin: 0;
    font-weight: 700;
    color: var(--ink);
    letter-spacing: 0.5px;
    white-space: nowrap;
  }
  .card-front .brand-name {
    position: absolute;
    left: 34px;
    top: 40px;
    font-size: 38px;
  }
  .contact {
    position: absolute;
    left: 33px;
    top: 160px;
    color: var(--white);
  }
  .person-name {
    margin: 0;
    font-size: 18px;
    font-weight: 700;
    line-height: 1.3;
  }
  .person-role {
    margin: 2px 0 0;
    font-size: 15px;
    line-height: 1.3;
  }
  .contact-list {
    list-style: none;
    margin: 20px 0 0;
    padding: 0;
    font-size: 15px;
    line-height: 20px;
  }
  .contact-list li {
    display: flex;
    align-items: center;
    gap: 8px;
  }
  .contact-list svg { flex: none; }
  .motto {
    margin: 18px 0 0;
    font-size: 15px;
    text-transform: uppercase;
    letter-spacing: 0.2px;
  }
  /* Back side */
  .card-back {
    left: 458px;
    top: 518px;
    width: 559px;
    height: 344px;
    background: var(--paper);
    border-radius: 60px 0 44px 0;
  }
  .card-back .brand-name {
    position: absolute;
    left: 117px;
    top: 136px;
    font-size: 42px;
  }
</style>
</head>
<body>
<main class="canvas">

  <section class="card card-front" aria-label="Business card, front">
    <div class="front-band"></div>
    <svg class="front-diagonal" width="556" height="147" viewBox="0 0 556 147" aria-hidden="true">
      <polygon points="393,147 556,147 556,0 551,0" fill="var(--ink)"/>
    </svg>
    <p class="brand-name">Satchel &amp; Sundial</p>
    <div class="contact">
      <h1 class="person-name">Dorota Falkner</h1>
      <p class="person-role">Your Lifestyle Business Coach Retreat &amp; Trip Leader</p>
      <ul class="contact-list">
        <li>
          <svg width="11" height="9" viewBox="0 0 11 9" aria-hidden="true">
            <rect x="0" y="0" width="11" height="9" rx="1" fill="var(--white)"/>
            <polyline points="0.5,0.8 5.5,5 10.5,0.8" fill="none" stroke="var(--ink)" stroke-width="1.2"/>
          </svg>
          hello@satchelandsundial.example
        </li>
        <li>
          <svg width="11" height="11" viewBox="0 0 11 11" aria-hidden="true">
            <circle cx="5.5" cy="5.5" r="5.5" fill="var(--white)"/>
            <path d="M5.5 0.5 C3 3,3 8,5.5 10.5 M5.5 0.5 C8 3,8 8,5.5 10.5 M0.5 5.5 H10.5" fill="none" stroke="var(--ink)" stroke-width="0.9"/>
          </svg>
          www.satchelandsundial.example
        </li>
      </ul>
      <p class="motto">Live a life you don't need a holiday from</p>
    </div>
  </section>

  <section class="card card-back" aria-label="Business card, back">
    <p class="brand-name">Satchel &amp; Sundial</p>
  </section>

</main>
</body>
</html>
```